Disability Magazine – Cover + Full Inside Layout

About the Publication

Our magazine is a quarterly, high‑impact publication that celebrates the lives, achievements, and everyday experiences of people with disabilities. It aims to inform, inspire, and advocate for accessibility, inclusion, and empowerment across all communities.

Target Audience

Adults (18‑65) with visible or invisible disabilities
Caregivers, family members, and allies
Professionals in health, education, policy, and design fields
Advocates and NGOs focused on accessibility

Project Goals

Visually compelling cover that instantly signals the magazine’s inclusive mission.
Consistent, readable interior layout for feature articles, interviews, photo essays, and resource guides.
Design that works both in print (A4, 300 dpi) and digitally (PDF/online flipbook).

```html
<!DOCTYPE html>
<html lang="en">
<head>
<meta charset="utf-8">
<title>Disability Magazine – Cover and Inside Spreads</title>
<link href="https://fonts.googleapis.com/css2?family=Oswald:wght@500;700&family=Montserrat:wght@400;600;700&family=Great+Vibes&display=swap" rel="stylesheet">
<style>
  :root{
    --stage:#e3e3e5;
    --paper:#f4f4f3;
    --ink:#262628;
    --ink-soft:#3a3a3d;
    --gold:#d8ad73;
    --muted:#8a8a8d;
    --ad:#e9e9ea;
    --head:'Oswald', sans-serif;
    --body:'Montserrat', sans-serif;
    --script:'Great Vibes', cursive;
  }
  *{box-sizing:border-box;margin:0;padding:0}
  html,body{width:1033px;height:1200px;overflow:hidden}
  body{background:var(--stage);font-family:var(--body);color:var(--ink)}
  .issue{display:grid;grid-template-columns:repeat(3,318px);grid-template-rows:repeat(5,220px);gap:14px 19px;padding:20px 19px}
  .spread{display:flex;width:318px;height:220px;box-shadow:0 4px 12px rgba(0,0,0,.18)}
  .page{position:relative;width:159px;height:220px;overflow:hidden;background:var(--paper)}
  .page.dark{background:var(--ink);color:#eee}
  .page.left{box-shadow:inset -6px 0 8px -6px rgba(0,0,0,.25)}
  .page.right{box-shadow:inset 6px 0 8px -6px rgba(0,0,0,.25)}
  .abs{position:absolute}
  .photo{position:absolute}
  .box{position:absolute;background:var(--ink);color:#eee;padding:5px}
  .box.light{background:var(--paper);color:var(--ink)}
  .masthead{position:absolute;top:6px;left:10px;font:700 4px var(--head);letter-spacing:.3px}
  .folio{position:absolute;top:12px;right:8px;width:5px;height:5px;background:var(--ink)}
  .dark .folio{background:var(--gold)}
  .title{font:700 11px/1 var(--head);text-transform:uppercase}
  .title .accent{color:var(--gold);display:block}
  .dark .title,.box .title{color:#fff}
  .rule{width:26px;height:1px;background:var(--gold);margin:2px 0 3px}
  .copy{font:400 3.6px/1.35 var(--body)}
  .copy b{font-weight:700;display:block;font-size:4px}
  .cols{display:grid;grid-template-columns:1fr 1fr;gap:5px}
  .ad{position:absolute;background:var(--ad);display:flex;align-items:center;justify-content:center;font:400 6px var(--body);color:#c4c4c6}
  .dark .ad{background:#fbfbfb}
  .script{font:400 8px var(--script)}
  .quote{font:600 6.5px/1.2 var(--body)}
  .vertical-title{writing-mode:vertical-rl;transform:rotate(180deg);font-size:14px;line-height:1.05;white-space:nowrap}
  /* cover */
  .cover-head{font:700 17px/.9 var(--head);text-transform:uppercase;color:var(--ink)}
  .cover-mast{font:700 30px/1 var(--head);color:#fff;letter-spacing:-.5px}
  .toc li{list-style:none;display:flex;gap:4px;align-items:baseline;margin-bottom:5px}
  .toc .num{font:700 8px var(--head)}
  .toc .item{font:600 3.8px var(--body);text-transform:uppercase}
  .bigletter{position:absolute;background:var(--ink)}
</style>
</head>
<body>
<main class="issue">

  <!-- 1 Cover -->
  <section class="spread">
    <div class="page left">
      <div class="photo" role="img" aria-label="Hiker with prosthetic leg and trekking poles on a grassy trail" style="left:0;top:22px;width:159px;height:150px;background:linear-gradient(160deg,#6f8f4a,#b9a584 55%,#e9e9e9)"></div>
      <p class="abs copy" style="top:5px;left:8px;font-size:3px">Quarterly edition · Inclusion · Access</p>
      <h2 class="abs cover-head" style="top:12px;left:8px;width:140px">Breaking the<br>Barriers</h2>
      <p class="abs copy" style="top:80px;left:98px;width:50px;color:#fff">Stories of strength, access and everyday wins from our readers.</p>
      <p class="abs copy" style="bottom:8px;left:8px;width:140px">Inside: athletes, advocates and a full resource guide.</p>
    </div>
    <div class="page right dark" style="background:linear-gradient(180deg,#1e1e20,#3c3c3f 70%,#d9d9d9)">
      <p class="abs copy" style="top:6px;left:40px;font-size:3px;color:#bbb">Lorem ipsum is simply dummy text</p>
      <h1 class="abs cover-mast" style="top:12px;left:8px">MAGAZINE</h1>
      <p class="abs" style="top:54px;left:8px;font:700 6px/1.1 var(--head);color:var(--gold)">THE BEST<br><span style="color:#fff">LEADERSHIP<br>SPORTS</span><br><span style="font-size:10px;color:#fff">2029</span></p>
      <div class="photo" role="img" aria-label="Smiling woman in a wheelchair raising a trophy" style="left:48px;top:50px;width:80px;height:130px;background:radial-gradient(ellipse at 50% 40%,#8c8c90,#3b3b3e 70%)"></div>
      <p class="abs" style="top:112px;right:8px;font:700 8px/1 var(--head);color:#fff;text-align:right">NAME<br>HERE</p>
      <p class="abs" style="bottom:26px;left:8px;font:700 6px/1 var(--head);color:var(--ink)">EXCLUSIVE<br>NAME HERE</p>
      <p class="abs" style="bottom:8px;right:8px;font:700 7px var(--head);color:var(--ink)">ABLEWAY</p>
    </div>
  </section>

  <!-- 2 Table of contents -->
  <section class="spread">
    <div class="page left">
      <div class="photo" role="img" aria-label="Sprinter with running blade on an athletics track" style="left:0;top:0;width:60px;height:160px;background:linear-gradient(180deg,#a8d6e0,#6d6a70 50%,#b07962)"></div>
      <span class="masthead" style="left:66px">MAGAZINE</span>
      <h2 class="abs title" style="top:16px;left:66px">Table of<br>Contents</h2>
      <ul class="abs toc" style="top:46px;left:66px;width:88px">
        <li><span class="num">04</span><span class="item">Lorem ipsum</span></li>
        <li><span class="num">05</span><span class="item">Lorem ipsum</span></li>
        <li><span class="num">06</span><span class="item">Lorem ipsum</span></li>
        <li><span class="num">07</span><span class="item">Lorem ipsum</span></li>
        <li><span class="num">08</span><span class="item">Lorem ipsum</span></li>
        <li><span class="num">09</span><span class="item">Lorem ipsum</span></li>
      </ul>
      <div class="box" style="left:0;bottom:0;width:159px;height:60px;padding:10px">
        <p style="font:700 4.5px/1.3 var(--head);color:var(--gold)">LOREM IPSUM DOLOR SIT AMET, CONSECTETUR ADIPISCING ELIT, SED DO EIUSMOD TEMPOR INCIDIDUNT UT LABORE ET DOLORE MAGNA ALIQUA.</p>
      </div>
    </div>
    <div class="page right">
      <span class="masthead">MAGAZINE</span><span class="folio"></span>
      <div class="photo" role="img" aria-label="Hiker with prosthetic leg smiling on a forest path" style="left:10px;top:22px;width:139px;height:140px;background:linear-gradient(170deg,#5d7d3e,#a7b38a 50%,#c0a27a)"></div>
      <div class="box" style="left:70px;top:100px;width:80px;height:110px">
        <p class="copy"><b>Lorem ipsum is simply</b>Short notes on training, travel and the gear that opens the trail to every walker.</p>
      </div>
    </div>
  </section>

  <!-- 3 Articles -->
  <section class="spread">
    <div class="page left">
      <span class="masthead">MAGAZINE</span>
      <h2 class="abs title" style="top:14px;left:10px">Articles<br>Content Here</h2>
      <div class="abs" style="top:40px;left:10px;width:62px">
        <p class="copy"><b>Lorem ipsum is simply</b>Every story here starts with a reader who found a new way to move, work and play.</p>
        <p class="copy" style="margin-top:4px"><b>Lorem ipsum is simply</b>Small changes in design make big changes in daily life for many.</p>
      </div>
      <div class="photo" role="img" aria-label="Archer in a wheelchair drawing a bow outdoors" style="left:80px;top:40px;width:79px;height:80px;background:linear-gradient(135deg,#3d4650,#b5a474 60%,#d7c9a0)"></div>
      <div class="abs" style="top:130px;left:80px;width:70px">
        <p class="copy"><b>Lorem ipsum is simply</b>Focus, patience and a steady arm carry every shot to the target.</p>
      </div>
    </div>
    <div class="page right">
      <span class="masthead">MAGAZINE</span><span class="folio"></span>
      <div class="photo" role="img" aria-label="Sunlit park with trees behind the archer" style="left:0;top:20px;width:100px;height:80px;background:linear-gradient(135deg,#c9b889,#8f8c5c)"></div>
      <div class="box" style="left:100px;top:30px;width:52px;height:110px">
        <p class="copy"><b>Lorem ipsum is simply</b>Training with adapted equipment keeps every athlete in the game all season.</p>
      </div>
      <p class="abs copy" style="left:10px;top:150px;width:140px">Local clubs now open their ranges to all, with ramps, lower stands and trained coaches ready to help.</p>
    </div>
  </section>

  <!-- 4 Interview -->
  <section class="spread">
    <div class="page left">
      <span class="masthead">MAGAZINE</span>
      <h2 class="abs title" style="top:14px;left:10px">Interview<br><span class="accent">Content Here</span></h2>
      <div class="abs" style="top:40px;left:10px;width:70px">
        <p class="copy"><b>Lorem ipsum is simply dummy ?</b>We ask what drives her to the track each morning.</p>
        <p class="copy" style="margin-top:3px"><b>Lorem ipsum is simply dummy ?</b>She talks about family, rest and her coach.</p>
      </div>
      <div class="photo" role="img" aria-label="Athlete with prosthetic leg stretching on a track" style="left:86px;top:30px;width:73px;height:80px;background:linear-gradient(160deg,#4a5a3c,#c06a5c 70%)"></div>
      <div class="box" style="left:0;top:150px;width:159px;height:50px">
        <div class="cols">
          <p class="copy"><b>Lorem ipsum is simply ?</b>Goals for the next season and beyond.</p>
          <p class="copy"><b>Lorem ipsum is simply ?</b>Advice for young athletes starting out.</p>
        </div>
      </div>
    </div>
    <div class="page right">
      <span class="masthead">MAGAZINE</span><span class="folio"></span>
      <div class="photo" role="img" aria-label="Hurdler with running blade mid-jump at an outdoor track" style="left:0;top:22px;width:159px;height:70px;background:linear-gradient(135deg,#3f5a35,#cfd1c9 60%,#c98676)"></div>
      <h2 class="abs title" style="top:96px;left:10px;font-size:9px">Interview<br>Content Here</h2>
      <div class="abs" style="top:120px;left:10px;width:65px">
        <p class="copy"><b>Lorem ipsum is simply dummy ?</b>How the team adapted every drill for all bodies.</p>
      </div>
      <div class="box" style="left:82px;top:112px;width:70px;height:90px">
        <p class="copy"><b>Lorem ipsum is simply dummy ?</b>Coaches share what changed once the club listened.</p>
        <p class="copy" style="margin-top:3px"><b>Lorem ipsum is simply dummy ?</b>Plans for a new indoor hall.</p>
      </div>
    </div>
  </section>

  <!-- 5 Dark articles -->
  <section class="spread">
    <div class="page left dark">
      <span class="masthead">MAGAZINE</span>
      <h2 class="abs title" style="top:14px;left:10px">Articles<br><span class="accent">Content Here</span></h2>
      <p class="abs copy" style="top:42px;left:10px;width:140px;color:#ccc">Racing chairs, fast hands and a packed stadium: the season opens with record crowds.</p>
      <div class="photo" role="img" aria-label="Wheelchair racer on a red track" style="left:10px;top:66px;width:44px;height:80px;background:linear-gradient(180deg,#a74a3a,#5a2b25)"></div>
      <div class="photo" role="img" aria-label="Wheelchair racer in blue on a green field" style="left:58px;top:66px;width:44px;height:80px;background:linear-gradient(180deg,#4d7b9a,#3c6d3a)"></div>
      <div class="photo" role="img" aria-label="Wheelchair racer on a red track near the finish" style="left:106px;top:66px;width:44px;height:80px;background:linear-gradient(180deg,#b55a46,#6a2d24)"></div>
      <p class="abs copy" style="top:152px;left:10px;width:44px"><b style="color:var(--gold)">Heading Here</b>Fast starts win races.</p>
      <p class="abs copy" style="top:152px;left:58px;width:44px"><b style="color:var(--gold)">Heading Here</b>Strong arms, light chair.</p>
      <p class="abs copy" style="top:152px;left:106px;width:44px"><b style="color:var(--gold)">Heading Here</b>Pace through the bend.</p>
    </div>
    <div class="page right">
      <div class="abs" style="left:0;top:0;width:100px;height:220px;background:var(--ink)"></div>
      <span class="masthead" style="color:#eee">MAGAZINE</span>
      <h2 class="abs title" style="top:22px;left:10px;color:#fff">Articles<br><span class="accent">Content Here</span></h2>
      <div class="photo" role="img" aria-label="Woman in a wheelchair training with boxing gloves" style="left:10px;top:60px;width:80px;height:140px;background:linear-gradient(160deg,#3a3a3d,#c85a68 55%,#2c2c2f)"></div>
      <div class="abs" style="left:104px;top:22px;width:50px">
        <p class="copy"><b>Lorem ipsum is simply ?</b>Boxing builds power and confidence in every session at the local gym.</p>
        <p class="copy" style="margin-top:4px">Coaches adapt footwork drills into chair drills with the same fierce focus.</p>
      </div>
    </div>
  </section>

  <!-- 6 Collage -->
  <section class="spread">
    <div class="page left">
      <span class="masthead">MAGAZINE</span>
      <div class="photo" role="img" aria-label="Swimmer on a starting block at an indoor pool" style="left:10px;top:18px;width:149px;height:60px;background:linear-gradient(135deg,#2d5a8c,#8ab4d6 60%,#d7c3a4)"></div>
      <div class="photo" role="img" aria-label="Wheelchair athlete on a red court" style="left:10px;top:84px;width:68px;height:100px;background:linear-gradient(180deg,#5c8a4a,#b8553e)"></div>
      <div class="photo" role="img" aria-label="Stadium stands with athletes" style="left:84px;top:84px;width:75px;height:46px;background:linear-gradient(135deg,#b54a3a,#3f6fae)"></div>
      <div class="photo" role="img" aria-label="Gym with adapted training equipment" style="left:84px;top:134px;width:75px;height:50px;background:linear-gradient(135deg,#c79a5a,#6a5a3a)"></div>
    </div>
    <div class="page right dark">
      <span class="masthead">MAGAZINE</span><span class="folio"></span>
      <div class="photo" role="img" aria-label="Two hikers with trekking poles on a rocky hill" style="left:10px;top:20px;width:80px;height:90px;background:linear-gradient(170deg,#c2d0dc,#8c9a6a 55%,#8a7a5c)"></div>
      <h2 class="abs title" style="top:116px;left:10px">Articles<br>Content Here</h2>
      <p class="abs copy" style="top:142px;left:10px;width:80px;color:#ccc">Two friends, one summit and a route planned for every step of the climb.</p>
      <div class="abs" style="left:96px;top:22px;width:56px">
        <p class="copy"><b>Lorem ipsum is simply ?</b>Trail maps now show slopes, rests and step-free paths.</p>
        <p class="copy" style="margin-top:4px"><b>Lorem ipsum is simply ?</b>Group hikes leave every first Sunday.</p>
      </div>
    </div>
  </section>

  <!-- 7 Vertical title -->
  <section class="spread">
    <div class="page left">
      <span class="masthead">MAGAZINE</span>
      <h2 class="abs title" style="top:14px;left:10px">Articles<br>Content Here</h2>
      <p class="abs copy" style="top:40px;left:10px;width:60px">Team sports bring people together on court and off it.</p>
      <p class="abs copy" style="top:18px;left:90px;width:62px">Wheelchair basketball leagues grow each year as new clubs open their doors to all.</p>
      <div class="photo" role="img" aria-label="Wheelchair basketball players reaching for the ball" style="left:10px;top:66px;width:72px;height:110px;background:linear-gradient(160deg,#d9a56a,#7a3e2a)"></div>
      <div class="photo" role="img" aria-label="Wheelchair racer outdoors" style="left:86px;top:66px;width:66px;height:56px;background:linear-gradient(170deg,#6f9a5a,#c0584a)"></div>
      <div class="photo" role="img" aria-label="Swimmer in a blue pool" style="left:86px;top:126px;width:66px;height:50px;background:linear-gradient(135deg,#2e8fc6,#a9dcf0)"></div>
    </div>
    <div class="page right">
      <span class="masthead">MAGAZINE</span><span class="folio"></span>
      <div class="box" style="left:10px;top:20px;width:44px;height:136px;display:flex;align-items:center;justify-content:center;padding:4px">
        <h2 class="title vertical-title">Articles<span class="accent">Content Here</span></h2>
      </div>
      <div class="photo" role="img" aria-label="Wheelchair racer on a red track" style="left:60px;top:20px;width:90px;height:70px;background:linear-gradient(170deg,#6f9a5a,#c0584a)"></div>
      <div class="abs" style="left:60px;top:96px;width:90px">
        <p class="copy"><b>• Lorem ipsum is simply</b>Chairs built for speed and grip.</p>
        <p class="copy" style="margin-top:3px"><b>• Lorem ipsum is simply</b>Clubs offer free trial days.</p>
      </div>
      <p class="abs copy" style="left:10px;top:166px;width:60px">Find a league near you in our resource guide at the back.</p>
      <div class="photo" role="img" aria-label="Swimmer racing in a pool lane" style="left:76px;top:150px;width:76px;height:50px;background:linear-gradient(135deg,#2e8fc6,#a9dcf0)"></div>
    </div>
  </section>

  <!-- 8 Photo essay -->
  <section class="spread">
    <div class="page left">
      <span class="masthead">MAGAZINE</span>
      <div class="photo" role="img" aria-label="Athlete with prosthetic leg doing a handstand on a pier at sunset" style="left:0;top:16px;width:159px;height:204px;background:linear-gradient(180deg,#d0d6dc,#8a8e94 50%,#6d5d50)"></div>
      <div class="box" style="left:96px;top:24px;width:56px;height:90px">
        <p class="copy"><b>Lorem ipsum</b>Balance, breath and strength come together at the water's edge.</p>
      </div>
      <div class="box" style="left:0;top:168px;width:80px;height:30px">
        <h2 class="title" style="font-size:8px">Articels<br><span class="accent">Content Here</span></h2>
      </div>
    </div>
    <div class="page right">
      <span class="masthead">MAGAZINE</span><span class="folio"></span>
      <div class="photo" role="img" aria-label="Hiker with prosthetic leg smiling outdoors" style="left:10px;top:22px;width:142px;height:80px;background:linear-gradient(170deg,#5d7d3e,#a7b38a 50%,#c0a27a)"></div>
      <div class="photo" role="img" aria-label="Archer in a wheelchair aiming" style="left:0;top:108px;width:80px;height:70px;background:linear-gradient(135deg,#3d4650,#b5a474 60%,#d7c9a0)"></div>
      <div class="abs" style="left:86px;top:110px;width:66px">
        <p class="copy"><b>Lorem ipsum</b>Outdoor sport gives every body room to grow and explore.</p>
      </div>
      <p class="abs copy" style="left:10px;top:184px;width:140px">Join a free weekend session and meet coaches who adapt every drill.</p>
    </div>
  </section>

  <!-- 9 Profile -->
  <section class="spread">
    <div class="page left">
      <span class="masthead">MAGAZINE</span>
      <div class="box" style="left:10px;top:16px;width:62px;height:190px">
        <div class="photo" role="img" aria-label="Portrait of a smiling man holding a basketball" style="left:5px;top:5px;width:52px;height:50px;background:linear-gradient(160deg,#5a7da0,#c49a7a)"></div>
        <p class="abs" style="left:5px;top:58px;font:700 5px var(--head);color:var(--gold)">NAME HERE</p>
        <p class="abs copy" style="left:5px;top:68px;width:52px">A player, coach and mentor who built his own city league.</p>
        <p class="abs script" style="left:5px;top:166px;color:#ddd">Signature</p>
        <p class="abs copy" style="left:20px;top:180px">(Player)</p>
      </div>
      <div class="abs cols" style="left:78px;top:18px;width:74px">
        <p class="copy">He started with four friends and one borrowed chair.</p>
        <p class="copy">Today the league counts forty teams.</p>
      </div>
      <div class="photo" role="img" aria-label="Wheelchair basketball player on an indoor court" style="left:78px;top:100px;width:74px;height:80px;background:linear-gradient(160deg,#6a8fb8,#b56e4e)"></div>
    </div>
    <div class="page right">
      <span class="masthead">MAGAZINE</span><span class="folio"></span>
      <div class="photo" role="img" aria-label="Runner with prosthetic leg in an orange top" style="left:10px;top:20px;width:60px;height:70px;background:linear-gradient(160deg,#2e2e30,#d06a4a 60%,#2e2e30)"></div>
      <div class="abs" style="left:76px;top:22px;width:76px">
        <p class="copy"><b>LOREM IPSUM IS SIMPLY DUMMY TEXT</b>Her first race came one year after surgery.</p>
      </div>
      <p class="abs copy" style="left:10px;top:96px;width:66px">She trains five days a week and still finds time to coach teens at her club.</p>
      <div class="box" style="left:80px;top:120px;width:79px;height:80px;padding:8px">
        <p class="quote">Lorem ipsum is simply dummy text of the printing and typesetting industry.</p>
      </div>
    </div>
  </section>

  <!-- 10 Resource guide -->
  <section class="spread">
    <div class="page left">
      <span class="masthead">MAGAZINE</span>
      <div class="photo" role="img" aria-label="Wheelchair basketball players reaching for the ball" style="left:10px;top:18px;width:149px;height:70px;background:linear-gradient(160deg,#d9a56a,#7a3e2a)"></div>
      <div class="photo" role="img" aria-label="Round inset of a wheelchair athlete" style="left:100px;top:70px;width:34px;height:34px;border-radius:50%;border:2px solid var(--paper);background:linear-gradient(135deg,#b5503e,#40536e)"></div>
      <h2 class="abs title" style="top:96px;left:10px;font-size:9px">Content Title Here</h2>
      <div class="abs rule" style="top:108px;left:10px"></div>
      <p class="abs copy" style="top:114px;left:10px;width:130px;font-size:4.2px">Lorem ipsum is simply dummy text of the printing and typesetting industry's standard.</p>
      <div class="abs cols" style="top:140px;left:10px;width:140px">
        <p class="copy">Teams train weekly at the community hall.</p>
        <p class="copy">New players welcome at every session.</p>
      </div>
    </div>
    <div class="page right">
      <span class="masthead">MAGAZINE</span><span class="folio"></span>
      <div class="box" style="left:10px;top:20px;width:80px;height:26px">
        <h2 class="title" style="font-size:8px">Our<br><span class="accent">Resource Guide</span></h2>
      </div>
      <div class="abs" style="left:10px;top:52px;width:62px">
        <p class="copy"><b>• Lorem ipsum is</b>Grants for adaptive gear.</p>
        <p class="copy" style="margin-top:4px"><b>• Lorem ipsum is</b>Accessible gyms nearby.</p>
        <p class="copy" style="margin-top:4px"><b>• Lorem ipsum is</b>Peer support groups.</p>
        <p class="copy" style="margin-top:4px"><b>• Lorem ipsum is</b>Transport and travel help.</p>
      </div>
      <div class="photo" role="img" aria-label="Man in a wheelchair lifting weights in a sunny gym" style="left:78px;top:50px;width:74px;height:110px;background:linear-gradient(160deg,#d6a56a,#e6e0d4 60%,#8b6a4a)"></div>
    </div>
  </section>

  <!-- 11 Ad spaces -->
  <section class="spread">
    <div class="page left dark">
      <span class="masthead">MAGAZINE</span>
      <div class="ad" style="left:10px;top:16px;width:70px;height:56px">Ad Here</div>
      <div class="ad" style="left:86px;top:16px;width:66px;height:130px">Ad Here</div>
      <div class="ad" style="left:10px;top:78px;width:70px;height:68px">Ad Here</div>
      <div class="ad" style="left:10px;top:152px;width:142px;height:52px">Ad Here</div>
    </div>
    <div class="page right">
      <span class="masthead" style="left:30px">MAGAZINE</span><span class="folio"></span>
      <div class="abs" style="left:0;top:0;width:22px;height:220px;background:var(--ink)"></div>
      <h2 class="abs title" style="top:20px;left:30px">Articles<br>Content Here</h2>
      <div class="abs cols" style="top:46px;left:30px;width:122px">
        <p class="copy"><b>Lorem ipsum</b>Sitting volleyball is fast, loud and open to all.</p>
        <p class="copy"><b>Lorem ipsum</b>Clubs lend gear for your first month.</p>
      </div>
      <div class="bigletter" style="left:24px;top:118px;width:44px;height:10px"></div>
      <div class="bigletter" style="left:24px;top:134px;width:44px;height:10px"></div>
      <div class="bigletter" style="left:24px;top:150px;width:44px;height:10px"></div>
      <div class="bigletter" style="left:24px;top:166px;width:44px;height:10px"></div>
      <div class="photo" role="img" aria-label="Volleyball player with prosthetic leg diving for the ball" style="left:70px;top:110px;width:82px;height:96px;background:linear-gradient(170deg,#e4e4e4,#3d6aa8 55%,#2a2a2c)"></div>
    </div>
  </section>

  <!-- 12 Bold feature + guide -->
  <section class="spread">
    <div class="page left">
      <span class="masthead">MAGAZINE</span>
      <div class="bigletter" style="left:10px;top:18px;width:30px;height:14px"></div>
      <div class="bigletter" style="left:130px;top:20px;width:29px;height:36px"></div>
      <h2 class="abs title" style="top:38px;left:10px">Articles<br>Content Here</h2>
      <p class="abs copy" style="top:64px;left:10px;width:70px">Lorem ipsum is simply dummy text of the printing industry.</p>
      <div class="bigletter" style="left:10px;top:88px;width:16px;height:40px"></div>
      <div class="bigletter" style="left:30px;top:88px;width:50px;height:40px;clip-path:polygon(0 0,25% 0,50% 60%,75% 0,100% 0,100% 100%,0 100%)"></div>
      <div class="photo" role="img" aria-label="Runner with prosthetic leg in an orange top holding a drink" style="left:84px;top:60px;width:75px;height:120px;background:linear-gradient(180deg,#f0f0f0,#d0684a 50%,#2a2a2c)"></div>
      <div class="abs cols" style="top:140px;left:10px;width:70px">
        <p class="copy">Race day starts at dawn.</p>
        <p class="copy">Recovery matters most.</p>
      </div>
    </div>
    <div class="page right dark">
      <span class="masthead">MAGAZINE</span><span class="folio"></span>
      <h2 class="abs title" style="top:20px;left:10px;font-size:12px">Our<br><span class="accent">Resource Guide</span></h2>
      <p class="abs quote" style="top:50px;left:10px;width:80px;font-weight:400">Lorem ipsum is simply dummy text of the.</p>
      <p class="abs copy" style="top:82px;left:10px;width:62px;color:#ccc">Helplines, grants and groups ready to support you and your family.</p>
      <div class="photo" role="img" aria-label="Silhouette of a person in a wheelchair in a misty gym" style="left:76px;top:64px;width:83px;height:106px;background:radial-gradient(ellipse at 60% 30%,#d8d2c8,#3a3835 70%)"></div>
      <div class="ad" style="left:10px;top:176px;width:142px;height:32px">Ad Here</div>
    </div>
  </section>

  <!-- 13 Quote feature -->
  <section class="spread">
    <div class="page left dark">
      <span class="masthead">MAGAZINE</span>
      <p class="abs quote" style="top:22px;left:10px;width:70px;font-weight:400;font-size:7px">Ipsum is simply dummy text of the printing and typesetting industry.</p>
      <div class="photo" role="img" aria-label="Man in a sports wheelchair raising a trophy" style="left:60px;top:70px;width:99px;height:140px;background:radial-gradient(ellipse at 50% 40%,#4a5570,#1f1f21 70%)"></div>
      <div class="box light" style="left:10px;top:130px;width:54px;height:50px">
        <p class="copy">A champion on court and a mentor to many new players.</p>
      </div>
    </div>
    <div class="page right">
      <span class="masthead" style="left:46px">MAGAZINE</span><span class="folio"></span>
      <div class="abs" style="left:0;top:0;width:40px;height:220px;background:var(--ink)"></div>
      <h2 class="abs title" style="top:30px;left:46px;font-size:12px">Articles<br>Content Here</h2>
      <p class="abs copy" style="top:60px;left:100px;width:52px;font-size:4.5px">Ipsum is simply dummy text of the printing industry.</p>
      <div class="abs" style="top:92px;left:46px;width:106px">
        <p class="copy">Lorem ipsum is simply dummy text. His story began in a small club gym with one coach who said yes.</p>
        <p class="copy" style="margin-top:4px">Now he trains the next generation and travels to every major tournament.</p>
        <p class="copy" style="margin-top:4px">He says the best win is seeing a new player score their first basket.</p>
      </div>
    </div>
  </section>

  <!-- 14 Photo spread -->
  <section class="spread">
    <div class="page left">
      <span class="masthead">MAGAZINE</span>
      <div class="photo" role="img" aria-label="Two athletes with prosthetic legs sitting on stadium grass, ad banner behind" style="left:0;top:16px;width:159px;height:204px;background:linear-gradient(180deg,#4a4660,#b2443e 35%,#5a8a3e 65%,#7aa850)"></div>
    </div>
    <div class="page right">
      <span class="masthead">MAGAZINE</span><span class="folio"></span>
      <div class="photo" role="img" aria-label="Athlete with prosthetic leg in an orange top" style="left:0;top:20px;width:80px;height:50px;background:linear-gradient(160deg,#2e2e30,#d06a4a)"></div>
      <div class="photo" role="img" aria-label="Swimmer on a starting block" style="left:84px;top:20px;width:68px;height:70px;background:linear-gradient(135deg,#2d5a8c,#8ab4d6)"></div>
      <div class="box" style="left:40px;top:74px;width:60px;height:136px">
        <h2 class="title" style="font-size:7px">Articles<br>Content Here</h2>
        <p class="copy" style="margin-top:3px">Ipsum is simply dummy text of the printing industry.</p>
        <p class="copy" style="margin-top:3px">Stadium days bring friends and rivals together.</p>
        <p class="script" style="margin-top:40px;font-size:6px">Signature</p>
      </div>
      <div class="photo" role="img" aria-label="Wheelchair basketball player" style="left:0;top:100px;width:38px;height:50px;background:linear-gradient(160deg,#d9a56a,#7a3e2a)"></div>
      <div class="photo" role="img" aria-label="Wheelchair racer on a track" style="left:104px;top:96px;width:48px;height:50px;background:linear-gradient(170deg,#6f9a5a,#c0584a)"></div>
      <p class="abs copy" style="left:104px;top:152px;width:48px">Finish lines for everyone.</p>
    </div>
  </section>

  <!-- 15 Guide with ads -->
  <section class="spread">
    <div class="page left">
      <span class="masthead">MAGAZINE</span>
      <div class="photo" role="img" aria-label="Hiker with prosthetic leg and trekking poles on a rocky trail" style="left:0;top:16px;width:90px;height:190px;background:linear-gradient(180deg,#7ea6c8,#c9c4b4 50%,#8a7a5c)"></div>
      <div class="photo" role="img" aria-label="Runner with prosthetic leg in a stadium" style="left:94px;top:22px;width:65px;height:70px;background:linear-gradient(160deg,#e8e8e8,#c06a4a 60%,#3a3a3d)"></div>
      <p class="abs script" style="left:94px;top:100px;color:var(--ink)">Heading Here</p>
      <p class="abs copy" style="left:94px;top:114px;width:60px">Trail tips for every level.</p>
      <div class="box" style="left:40px;top:160px;width:60px;height:40px">
        <p class="copy">Pack light, plan rests and hike with a friend.</p>
      </div>
    </div>
    <div class="page right">
      <span class="masthead">MAGAZINE</span><span class="folio"></span>
      <p class="abs script" style="left:10px;top:20px">Heading Here</p>
      <p class="abs copy" style="left:10px;top:34px;width:64px">Find accessible routes and rest stops near you.</p>
      <div class="ad" style="left:10px;top:52px;width:64px;height:40px">Ad Here</div>
      <div class="ad" style="left:84px;top:20px;width:68px;height:50px">Ad Here</div>
      <p class="abs script" style="left:10px;top:98px">Heading Here</p>
      <p class="abs copy" style="left:10px;top:112px;width:64px">Gear libraries lend poles and chairs.</p>
      <div class="ad" style="left:10px;top:128px;width:64px;height:40px">Ad Here</div>
      <p class="abs script" style="left:84px;top:78px">Heading Here</p>
      <p class="abs copy" style="left:84px;top:92px;width:68px">Guided walks run every weekend.</p>
      <div class="ad" style="left:84px;top:110px;width:68px;height:60px">Ad Here</div>
      <p class="abs copy" style="left:10px;top:180px;width:142px">Lorem ipsum is simply dummy text of the printing industry.</p>
    </div>
  </section>

</main>
</body>
</html>
```